Business Card Design

We would like to re-design our business cards. Our Company - Qwinrel Turbochargers, rebuilds turbochargers and sells replacement parts. Our website is: http://www.qwinrelturbochargers-example.com
We just had our logo changed. I will attach the file. Looking for fresh new/modern business card. We like the colors red, black, white and silver. Black background looks attractive, but not a requirement. The final design should communicate reasonable/competitive prices, top quality and reliability of our products.
Updates
Project Deadline Extended
Reason: Need to finalize the info on the card. Currently working on changing address and email info. Want to make sure it is the correct one before accepting the final design. Unless, this is something that can be changed at a later time..??
Industry/Entity Type
Business
Contact Information for Business Card
QWINREL TURBOCHARGERS, LLC
20473 Harwick Lane NE
Massillon, OH 44647
Tel: +1-555-214-7390
Fax: +1-555-267-1842
info@QwinrelTurbochargers-example.com
Our current business card had the following highlights:
*We rebuild all Turbocharges for Automotive, Diesel and Industrial
*Precision Balancing and in-house turbocharger needs
*All Turbocharger replacement parts are made in USA / U.K.
Look and feel
Each slider illustrates characteristics of the customer's brand and the style your logo design should communicate.

```html
<!DOCTYPE html>
<html lang="en">
<head>
<meta charset="utf-8">
<title>Qwinrel Turbochargers – Business Card</title>
<link rel="stylesheet" href="https://fonts.googleapis.com/css2?family=Open+Sans:wght@400;600;700&display=swap">
<style>
  :root {
    --page: #ece8e2;
    --red: #e8222f;
    --white: #ffffff;
    --black: #121011;
    --ink: #2a2a2a;
    --grey: #8a8a8a;
    --silver: #9c9c9c;
  }
  * { margin: 0; padding: 0; box-sizing: border-box; }
  html, body { width: 1200px; height: 1023px; overflow: hidden; }
  body {
    background: var(--page);
    font-family: "Open Sans", Arial, sans-serif;
    position: relative;
  }
  .card {
    position: absolute;
    width: 600px;
    height: 343px;
    overflow: hidden;
    box-shadow: 0 6px 18px rgba(0,0,0,.18);
  }

  /* Front */
  .card-front { left: 90px; top: 110px; background: var(--white); }
  .front-red {
    position: absolute; top: 0; right: 0; bottom: 0; left: 340px;
    background: var(--red);
  }
  .front-divider {
    position: absolute; top: 0; bottom: 0; left: 330px; width: 24px; height: 343px;
  }
  .brand-front {
    position: absolute; left: 40px; top: 36px;
    display: flex; align-items: center; gap: 12px;
  }
  .brand-dot { width: 16px; height: 16px; border-radius: 50%; background: var(--red); flex: none; }
  .brand-name {
    font-weight: 700; font-size: 24px; color: var(--ink); line-height: 1.1;
  }
  .person { position: absolute; left: 40px; top: 150px; }
  .person-name { font-size: 26px; color: var(--red); font-weight: 400; line-height: 1.2; }
  .person-title { font-size: 14px; color: var(--ink); margin-top: 2px; }
  .contacts {
    position: absolute; left: 40px; top: 226px; list-style: none;
    font-size: 13px; color: var(--ink); white-space: nowrap;
  }
  .contacts li { display: flex; align-items: center; gap: 9px; height: 22px; }
  .contacts svg { width: 13px; height: 13px; flex: none; }
  .front-company {
    position: absolute; right: 26px; top: 36px;
    text-align: right; font-size: 18px; font-weight: 700; color: var(--white);
    white-space: nowrap;
  }
  .address {
    position: absolute; right: 26px; bottom: 36px;
    text-align: right; font-size: 15px; color: var(--white); line-height: 1.4;
    font-style: normal; white-space: nowrap;
  }

  /* Back */
  .card-back {
    left: 510px; top: 560px;
    background: linear-gradient(160deg, #1f1c1d 0%, var(--black) 60%);
  }
  .brand-back {
    position: absolute; left: 0; right: 0; top: 130px;
    display: flex; justify-content: center; align-items: center; gap: 14px;
  }
  .brand-back .brand-dot { background: var(--silver); width: 20px; height: 20px; }
  .brand-back .brand-name { color: var(--red); font-size: 32px; }
  .web-back {
    position: absolute; left: 0; right: 0; bottom: 42px;
    display: flex; align-items: center; justify-content: center; gap: 16px;
    font-size: 14px; color: var(--grey);
  }
  .web-back .rule { width: 70px; height: 1px; background: var(--red); }
  .web-back .accent { color: var(--red); }
</style>
</head>
<body>

<section class="card card-front" aria-label="Business card front">
  <div class="front-red"></div>
  <svg class="front-divider" viewBox="0 0 24 343" preserveAspectRatio="none" aria-hidden="true">
    <polygon points="0,0 10,0 24,343 14,343" fill="#121011"/>
  </svg>

  <div class="brand-front">
    <span class="brand-dot"></span>
    <span class="brand-name">Qwinrel<br>Turbochargers</span>
  </div>

  <div class="person">
    <p class="person-name">Marlen Quist</p>
    <p class="person-title">Director</p>
  </div>

  <ul class="contacts">
    <li>
      <svg viewBox="0 0 16 16" aria-hidden="true"><path d="M3 1h3l1 4-2 1c1 2 2 3 4 4l1-2 4 1v3c0 1-1 2-2 2C7 14 2 9 2 3c0-1 0-2 1-2z" fill="#e8222f"/></svg>
      +1-555-214-7390
    </li>
    <li>
      <svg viewBox="0 0 16 16" aria-hidden="true"><rect x="4" y="1" width="8" height="5" fill="#e8222f"/><rect x="1" y="6" width="14" height="7" rx="1" fill="#e8222f"/><rect x="4" y="10" width="8" height="5" fill="#ffffff" stroke="#e8222f"/></svg>
      +1-555-267-1842
    </li>
    <li>
      <svg viewBox="0 0 16 16" aria-hidden="true"><rect x="1" y="3" width="14" height="10" fill="#e8222f"/><path d="M1 3l7 6 7-6" stroke="#fff" stroke-width="1.4" fill="none"/></svg>
      info@QwinrelTurbochargers-example.com
    </li>
    <li>
      <svg viewBox="0 0 16 16" aria-hidden="true"><circle cx="8" cy="8" r="7" fill="#e8222f"/><path d="M1 8h14M8 1v14M3 4h10M3 12h10" stroke="#fff" stroke-width="1"/><ellipse cx="8" cy="8" rx="3" ry="7" stroke="#fff" stroke-width="1" fill="none"/></svg>
      www.qwinrelturbochargers-example.com
    </li>
  </ul>

  <p class="front-company">Qwinrel Turbochargers</p>
  <address class="address">
    5182 Orchard Bend Ave. NW<br>
    North Calder, Ohio
  </address>
</section>

<section class="card card-back" aria-label="Business card back">
  <div class="brand-back">
    <span class="brand-dot"></span>
    <span class="brand-name">Qwinrel Turbochargers</span>
  </div>
  <div class="web-back">
    <span class="rule"></span>
    <span>www.<span class="accent">qwinrelturbochargers-example</span>.com</span>
    <span class="rule"></span>
  </div>
</section>

</body>
</html>
```